Looking for a modern, Professional business card design

We have a simple business card, but are looking for a more modern, professional look. A sample of the basic card is attached as well as the logo. We would also like to add that we offer:
Struggling with your finances?
- Learn to become debt free
- Discover the power of cash
- Control your money instead of it controlling you
Let us help you achieve a new level of financial freedom!
Also, we would like to have a "SPECIAL OFFER!: FREE 30 minute consultation"
Financial Planning

```html
<!DOCTYPE html>
<html lang="en">
<head>
<meta charset="UTF-8">
<title>Harbor Money Coaching – Business Card</title>
<link href="https://fonts.googleapis.com/css2?family=Josefin+Sans:wght@400;600;700&family=Russo+One&display=swap" rel="stylesheet">
<style>
  :root {
    --bg: #2b2b2d;
    --card: #ffffff;
    --green: #3b9a3f;
    --green-dark: #2f7f33;
    --green-light: #8dc63f;
    --lime: #a6d94e;
    --ink: #1c1c1c;
    --white: #ffffff;
  }
  * { box-sizing: border-box; margin: 0; padding: 0; }
  html, body { width: 1200px; height: 900px; overflow: hidden; }
  body {
    background: var(--bg);
    font-family: "Josefin Sans", sans-serif;
    color: var(--ink);
    position: relative;
  }
  .card {
    position: absolute;
    width: 620px;
    height: 355px;
    background: var(--card);
    border-radius: 22px;
    overflow: hidden;
    box-shadow: 0 18px 40px rgba(0,0,0,.45);
  }
  .card--back { left: 90px; top: 70px; text-align: center; }
  .card--front { left: 490px; top: 470px; }

  .brand {
    display: inline-flex;
    align-items: center;
    gap: 10px;
    font-family: "Josefin Sans", sans-serif;
    font-weight: 700;
    color: var(--green-dark);
    text-transform: uppercase;
    letter-spacing: .5px;
  }
  .brand__dot { border-radius: 50%; background: var(--green-light); flex: none; }

  /* back */
  .card--back .brand { margin-top: 62px; font-size: 30px; }
  .card--back .brand__dot { width: 22px; height: 22px; }
  .site { font-size: 15px; margin-top: 12px; }
  .site em { font-style: normal; color: var(--green); }
  .pill {
    display: inline-block;
    margin-top: 8px;
    padding: 5px 14px 2px;
    border: 2px solid var(--ink);
    border-radius: 20px;
    font-size: 17px;
    text-transform: uppercase;
  }
  .pill .hl { color: var(--green); }
  .benefits { list-style: none; margin-top: 10px; font-size: 17px; line-height: 1.4; }
  .benefits strong { color: var(--green); font-weight: 700; text-transform: uppercase; }

  /* front */
  .band { position: absolute; inset: 0; width: 100%; height: 100%; }
  .corner-tab { position: absolute; right: 0; top: 0; width: 26px; height: 44px; background: var(--green-light); }
  .person { position: absolute; right: 40px; top: 30px; text-align: right; }
  .person__name { font-family: "Russo One", sans-serif; font-size: 24px; color: var(--green-light); letter-spacing: 1px; text-transform: uppercase; }
  .person__role { font-family: "Russo One", sans-serif; font-size: 13px; letter-spacing: .8px; text-transform: uppercase; margin-top: 4px; }
  .card--front .brand { position: absolute; left: 40px; top: 110px; font-size: 28px; }
  .card--front .brand__dot { width: 20px; height: 20px; }
  .offer { position: absolute; left: 40px; top: 168px; font-size: 20px; white-space: nowrap; }
  .offer__tag { font-family: "Russo One", sans-serif; font-size: 15px; color: var(--green-light); text-transform: uppercase; }
  .offer__free { font-family: "Russo One", sans-serif; font-size: 15px; text-transform: uppercase; }
  .offer__rest { color: var(--green-light); }
  .contacts { position: absolute; left: 40px; top: 228px; list-style: none; color: var(--white); font-size: 20px; line-height: 1.55; }
  .contacts li { display: flex; align-items: center; gap: 14px; }
  .contacts svg { width: 14px; height: 14px; flex: none; }
  .contacts em { font-style: normal; color: var(--lime); }
</style>
</head>
<body>

<section class="card card--back">
  <div class="brand"><span class="brand__dot"></span>Harbor Money Coaching</div>
  <p class="site">www.<em>calmmoneypath</em>.com</p>
  <p class="pill"><span class="hl">Struggling</span> with your <span class="hl">finances?</span></p>
  <ul class="benefits">
    <li>Learn to become debt free</li>
    <li>Discover the power of cash</li>
    <li>Control your money instead of it controlling you</li>
    <li>Let us help you achieve a new level of financial <strong>freedom!</strong></li>
  </ul>
</section>

<section class="card card--front">
  <svg class="band" viewBox="0 0 620 355" preserveAspectRatio="none" aria-hidden="true">
    <path d="M0 200 H330 C420 200 470 150 620 150 V355 H0 Z" fill="var(--green)"/>
    <path d="M330 200 C420 200 470 150 620 150 V160 C480 160 430 200 360 206 Z" fill="var(--green-dark)" opacity=".5"/>
  </svg>
  <div class="corner-tab"></div>
  <div class="person">
    <p class="person__name">Daniel R. Hayes</p>
    <p class="person__role">Personal Financial Coach</p>
  </div>
  <div class="brand"><span class="brand__dot"></span>Harbor Money Coaching</div>
  <p class="offer"><span class="offer__tag">Special offer!</span> <span class="offer__free">Free</span> 30 <span class="offer__rest">minute consultation</span></p>
  <ul class="contacts">
    <li><svg viewBox="0 0 14 14"><rect x="3" y="0.5" width="8" height="13" rx="1.5" fill="none" stroke="var(--lime)" stroke-width="1.4"/><circle cx="7" cy="11" r=".9" fill="var(--lime)"/></svg>(205) 555-0182</li>
    <li><svg viewBox="0 0 14 14"><rect x="1" y="3" width="12" height="8" rx="1" fill="none" stroke="var(--lime)" stroke-width="1.4"/><path d="M1 3 L7 8 L13 3" fill="none" stroke="var(--lime)" stroke-width="1.4"/></svg>daniel@calmmoneypath.com</li>
    <li><svg viewBox="0 0 14 14"><circle cx="7" cy="7" r="6" fill="none" stroke="var(--lime)" stroke-width="1.3"/><path d="M1 7 H13 M7 1 C4 4 4 10 7 13 M7 1 C10 4 10 10 7 13" fill="none" stroke="var(--lime)" stroke-width="1"/></svg>www.<em>calmmoneypath</em>.com</li>
  </ul>
</section>

</body>
</html>
```